Redesign of business card for Cedar Ridge Mechanical

We are looking for a new design for our business cards for Cedar Ridge Mechanical. We are a plumbing & HVAC construction company, operating on the West Coast of Canada and USA. Logo attached.
Industry/Entity Type
Construction - Plumbing & HVAC
Contact Information for Business Card
Name, address, phone numbers, email, website address
Look and feel
Each slider illustrates characteristics of the customer's brand and the style your logo design should communicate.

```html
<!DOCTYPE html>
<html lang="en">
<head>
<meta charset="utf-8">
<title>Cedar Ridge Mechanical – Business Card</title>
<link href="https://fonts.googleapis.com/css2?family=Montserrat:wght@400;600;700&display=swap" rel="stylesheet">
<style>
  :root {
    --page-bg: #d8d3cb;
    --card-bg-top: #f1ede6;
    --card-bg-bottom: #e6e0d6;
    --ink: #1a1a1a;
    --band: #0d0d0d;
    --swoosh-light: #bdb6ab;
    --swoosh-dark: #6f6a63;
    --gold: #d6c29e;
    --soft-gold: #cdbfa8;
  }
  * { margin: 0; padding: 0; box-sizing: border-box; }
  html, body {
    width: 1200px;
    height: 1047px;
    overflow: hidden;
    background: var(--page-bg);
    font-family: "Montserrat", sans-serif;
  }
  .business-card {
    position: absolute;
    left: 80px;
    top: 241px;
    width: 1040px;
    height: 565px;
    border-radius: 17px;
    overflow: hidden;
    background: linear-gradient(180deg, var(--card-bg-top), var(--card-bg-bottom));
    box-shadow: 0 10px 30px rgba(0,0,0,0.12);
  }
  .card-waves {
    position: absolute;
    inset: 0;
    width: 100%;
    height: 100%;
  }
  .brand {
    position: absolute;
    right: 49px;
    top: 150px;
    display: flex;
    align-items: center;
    gap: 16px;
  }
  .brand-square {
    width: 22px;
    height: 22px;
    background: var(--ink);
  }
  .brand-name {
    font-size: 30px;
    font-weight: 600;
    color: var(--ink);
    letter-spacing: 1px;
  }
  .person {
    position: absolute;
    left: 61px;
    top: 297px;
  }
  .person-name {
    font-size: 33px;
    font-weight: 700;
    color: var(--gold);
    letter-spacing: 0.5px;
  }
  .person-title {
    margin-top: 6px;
    font-size: 25px;
    font-weight: 400;
    color: var(--soft-gold);
  }
  .contact-list {
    position: absolute;
    left: 61px;
    top: 415px;
    list-style: none;
  }
  .contact-item {
    display: flex;
    align-items: center;
    gap: 8px;
    height: 40px;
    font-size: 25px;
    color: var(--soft-gold);
  }
  .contact-icon {
    width: 22px;
    height: 22px;
    flex: none;
  }
  .address {
    position: absolute;
    right: 49px;
    top: 451px;
    text-align: right;
    font-size: 25px;
    line-height: 40px;
    color: var(--soft-gold);
  }
</style>
</head>
<body>
  <div class="business-card">
    <svg class="card-waves" viewBox="0 0 880 478" preserveAspectRatio="none" aria-hidden="true">
      <defs>
        <linearGradient id="swooshGradient" x1="0" y1="0" x2="1" y2="0">
          <stop offset="0" stop-color="var(--swoosh-dark)"/>
          <stop offset="0.45" stop-color="var(--swoosh-light)"/>
          <stop offset="1" stop-color="var(--swoosh-dark)"/>
        </linearGradient>
        <linearGradient id="bandGradient" x1="0" y1="0" x2="0" y2="1">
          <stop offset="0" stop-color="#1c1c1c"/>
          <stop offset="1" stop-color="var(--band)"/>
        </linearGradient>
      </defs>
      <path class="swoosh" fill="url(#swooshGradient)"
        d="M10,214 C140,150 250,148 350,170 C480,200 590,306 720,314 C800,318 850,300 872,286 C845,314 792,338 700,334 C560,322 450,202 330,178 C220,156 120,182 0,236 Z"/>
      <path class="band" fill="url(#bandGradient)"
        d="M0,236 C120,182 220,156 330,178 C450,202 560,322 700,334 C792,338 845,314 880,292 L880,478 L0,478 Z"/>
    </svg>

    <div class="brand">
      <span class="brand-square"></span>
      <span class="brand-name">CEDAR RIDGE MECHANICAL</span>
    </div>

    <div class="person">
      <div class="person-name">DANIEL REED</div>
      <div class="person-title">Managing Director</div>
    </div>

    <ul class="contact-list">
      <li class="contact-item">
        <svg class="contact-icon" viewBox="0 0 24 24" aria-hidden="true">
          <path fill="var(--soft-gold)" d="M6.6 10.8a15.1 15.1 0 0 0 6.6 6.6l2.2-2.2a1 1 0 0 1 1-.25 11.4 11.4 0 0 0 3.6.57 1 1 0 0 1 1 1V20a1 1 0 0 1-1 1A17 17 0 0 1 3 4a1 1 0 0 1 1-1h3.5a1 1 0 0 1 1 1c0 1.25.2 2.45.57 3.57a1 1 0 0 1-.25 1z"/>
        </svg>
        <span>123 456 789</span>
      </li>
      <li class="contact-item">
        <svg class="contact-icon" viewBox="0 0 24 24" aria-hidden="true">
          <rect x="3" y="6" width="18" height="13" rx="1.5" fill="none" stroke="var(--soft-gold)" stroke-width="2"/>
          <path d="M3.5 7l8.5 6.5L20.5 7" fill="none" stroke="var(--soft-gold)" stroke-width="2"/>
        </svg>
        <span>info@yourgmail.com</span>
      </li>
      <li class="contact-item">
        <svg class="contact-icon" viewBox="0 0 24 24" aria-hidden="true">
          <circle cx="12" cy="12" r="9" fill="none" stroke="var(--soft-gold)" stroke-width="2"/>
          <path d="M3 12h18M12 3c3 3 3 15 0 18M12 3c-3 3-3 15 0 18" fill="none" stroke="var(--soft-gold)" stroke-width="1.6"/>
        </svg>
        <span>www.yourwebsite.com</span>
      </li>
    </ul>

    <div class="address">
      <div>Your address, City</div>
      <div>State, Zip 1234</div>
    </div>
  </div>
</body>
</html>
```